Business Card Design

New business card design

Target Market(s)

Residential & Commercial Property Managers

Industry/Entity Type

Plumbing Services

Contact Information for Business Card

Name - Rowan Keddle, title - Director, Phone Number - 0431 286 517, email - rowan@tbk-plumbing.com.au, Company ABN - 73 215 904 386,

Font styles to use
Sans Serif

Colors
0054AA
0677BA
7BADD7
CADEEF
E8F1F8

```html
<!DOCTYPE html>
<html lang="en">
<head>
<meta charset="utf-8">
<title>TBK Plumbing Services – Business Card</title>
<link href="https://fonts.googleapis.com/css2?family=Montserrat:wght@400;500;700&display=swap" rel="stylesheet">
<style>
  :root {
    --stage: #c9c8c5;
    --card-white: #ffffff;
    --navy: #1d242c;
    --sky: #29a9e0;
    --ink-soft: #6b6f74;
    --white: #ffffff;
  }
  * { box-sizing: border-box; margin: 0; padding: 0; }
  html, body {
    width: 1200px; height: 801px; overflow: hidden;
    background: var(--stage);
    font-family: "Montserrat", Arial, sans-serif;
  }
  .stage {
    position: relative; width: 1200px; height: 801px;
  }
  .card {
    position: absolute; top: 246px;
    width: 540px; height: 309px;
    overflow: hidden;
    box-shadow: 0 14px 30px rgba(0,0,0,0.22);
  }
  .card--front { left: 40px; background: var(--card-white); }
  .card--back { left: 620px; background: var(--navy); }

  /* brand name block */
  .brand { position: absolute; text-align: center; font-weight: 500; line-height: 1; }
  .brand__name { display: flex; align-items: center; justify-content: center; gap: 10px; }
  .brand__dot { border-radius: 50%; background: var(--sky); display: inline-block; }
  .brand__tag { display: block; }

  .card--front .brand { left: 90px; top: 34px; width: 320px; color: var(--navy); }
  .card--front .brand__name { font-size: 66px; letter-spacing: -1px; }
  .card--front .brand__dot { width: 14px; height: 14px; margin-top: 22px; }
  .card--front .brand__tag { font-size: 11px; letter-spacing: 6px; margin-top: 14px; }

  .card--back .brand { left: 60px; top: 88px; width: 420px; color: var(--white); }
  .card--back .brand__name { font-size: 104px; letter-spacing: -2px; }
  .card--back .brand__dot { width: 20px; height: 20px; margin-top: 36px; }
  .card--back .brand__tag { font-size: 14px; letter-spacing: 10px; margin-top: 20px; }

  /* front bands */
  .band { position: absolute; top: 170px; height: 99px; }
  .band--name { left: 0; width: 286px; background: var(--navy); }
  .band--contact { left: 286px; width: 254px; background: var(--sky); }

  .person { position: absolute; right: 18px; top: 26px; text-align: right; }
  .person__name { color: var(--sky); font-weight: 700; font-size: 24px; line-height: 1; }
  .person__title { color: var(--white); font-weight: 400; font-size: 13px; margin-top: 4px; }

  .contact { position: absolute; left: 20px; top: 17px; list-style: none; color: var(--white); font-size: 12px; }
  .contact__item { display: flex; align-items: center; gap: 6px; height: 22px; }
  .contact__icon { width: 11px; height: 11px; fill: var(--white); flex: none; }
</style>
</head>
<body>
<main class="stage">
  <section class="card card--front" aria-label="Business card front">
    <div class="brand">
      <span class="brand__name">tbk<span class="brand__dot"></span></span>
      <span class="brand__tag">plumbing services</span>
    </div>
    <div class="band band--name">
      <div class="person">
        <p class="person__name">Rowan Keddle</p>
        <p class="person__title">Director</p>
      </div>
    </div>
    <div class="band band--contact">
      <ul class="contact">
        <li class="contact__item">ABN - 73 215 904 386</li>
        <li class="contact__item">
          <svg class="contact__icon" viewBox="0 0 24 24" aria-hidden="true"><path d="M6.6 10.8a15.1 15.1 0 0 0 6.6 6.6l2.2-2.2a1 1 0 0 1 1-.25 11.4 11.4 0 0 0 3.6.57 1 1 0 0 1 1 1V20a1 1 0 0 1-1 1A17 17 0 0 1 3 4a1 1 0 0 1 1-1h3.5a1 1 0 0 1 1 1c0 1.25.2 2.45.57 3.57a1 1 0 0 1-.25 1z"/></svg>
          0431 286 517
        </li>
        <li class="contact__item">
          <svg class="contact__icon" viewBox="0 0 24 24" aria-hidden="true"><path d="M2 5h20v14H2zm2 2v.5l8 5 8-5V7l-8 5z"/></svg>
          rowan@tbk-plumbing.com.au
        </li>
      </ul>
    </div>
  </section>

  <section class="card card--back" aria-label="Business card back">
    <div class="brand">
      <span class="brand__name">tbk<span class="brand__dot"></span></span>
      <span class="brand__tag">plumbing services</span>
    </div>
  </section>
</main>
</body>
</html>
```